Dietitian needs awesome business card

I need a contemporary design that's eye catching but professional.
My card is to given to doctors, specialists and patients alike.
I manage patients with chronic diseases
I have uploaded my logo and current business card, I would also like the other Certified Clinical Nutritionist logo incorporated into the design

Target Market(s)

Doctors, specialists and patients

Industry/Entity Type

Healthcare

Contact Information for Business Card

www.brightfieldnutrition.com.au
Ph: 0427 561 903
Fax: 6457 2183
email: marcus.k.diet@fernmail.com
Space on the back of the card with: Appointment date, Appointment time and appointment location

Font styles to use
Serif

Colors
fbee3e
876aae
ffc214

Requirements
Must have
• My Logo
• Certified Clinical Nutritionist Logo
• My 4 locations - Pinebrook Medical Centre, North Corrin Health, Hollis Medical, Ashcombe Doctors Surgery
Nice to have
• I like the colours in my current business card

```html
<!DOCTYPE html>
<html lang="en">
<head>
<meta charset="utf-8">
<title>Brightfield Nutrition &amp; Dietetics – Business Card</title>
<link rel="stylesheet" href="https://fonts.googleapis.com/css2?family=Arimo:wght@400;700&display=swap">
<style>
  :root {
    --backdrop: #3a3431;
    --card: #1b1b1d;
    --blue: #2452c4;
    --green: #8cc63f;
    --orange: #f47b20;
    --ink: #f2f2f2;
    --rule: #8a8a8e;
  }
  * { box-sizing: border-box; margin: 0; padding: 0; }
  html, body { width: 1200px; height: 787px; overflow: hidden; }
  body {
    background: var(--backdrop);
    font-family: "Arimo", Arial, sans-serif;
    position: relative;
  }
  .card {
    position: absolute;
    top: 244px;
    width: 520px;
    height: 298px;
    background: var(--card);
    border-radius: 4px;
    box-shadow: 0 10px 30px rgba(0,0,0,.45);
    overflow: hidden;
  }
  .card--back { left: 50px; }
  .card--front { left: 630px; }

  /* brand lockup */
  .brand { position: absolute; display: flex; align-items: center; gap: 8px; }
  .brand__dot { width: 26px; height: 26px; border-radius: 50%; background: var(--green); flex: none; }
  .brand__name { color: var(--blue); font-weight: 700; line-height: 1.05; white-space: nowrap; }
  .card--back .brand { left: 18px; top: 16px; }
  .card--back .brand__name { font-size: 15px; }
  .card--front .brand { left: 26px; top: 124px; }
  .card--front .brand__dot { width: 36px; height: 36px; }
  .card--front .brand__name { font-size: 17px; }

  /* back: appointment form */
  .form-line { position: absolute; left: 22px; right: 160px; height: 1px; background: var(--rule); }
  .form-label { position: absolute; color: var(--blue); font-size: 13px; }
  .form-ampm { position: absolute; color: var(--blue); font-size: 11px; }
  .badge {
    position: absolute; right: 22px; top: 60px;
    width: 120px; height: 56px; background: var(--orange);
    display: flex; align-items: center; justify-content: space-between;
    padding: 0 10px;
  }
  .badge__text { color: #fff; font-size: 9px; line-height: 1.2; width: 62px; }
  .badge__seal { width: 34px; height: 34px; border-radius: 50%; background: #fff; }
  .locations { position: absolute; list-style: none; color: var(--ink); font-size: 12px; }
  .locations li { display: flex; align-items: center; gap: 7px; margin-bottom: 8px; }
  .locations li::before {
    content: ""; width: 10px; height: 10px; border: 1px solid var(--ink); flex: none;
  }
  .locations--left { left: 22px; top: 218px; }
  .locations--right { left: 270px; top: 218px; }

  /* front: contact panel */
  .divider {
    position: absolute; left: 278px; top: 50px; width: 1px; height: 200px;
    background: linear-gradient(transparent, #9a9aa0 30%, #9a9aa0 70%, transparent);
  }
  .person { position: absolute; left: 296px; top: 68px; }
  .person__name { color: var(--blue); font-size: 20px; font-weight: 400; letter-spacing: .5px; white-space: nowrap; }
  .person__role { color: var(--green); font-size: 14px; font-weight: 700; margin-top: 4px; }
  .contacts { position: absolute; left: 296px; top: 130px; list-style: none; color: var(--ink); font-size: 12px; }
  .contacts li { display: flex; align-items: center; gap: 8px; margin-bottom: 10px; white-space: nowrap; }
  .contacts svg { width: 12px; height: 12px; fill: var(--blue); flex: none; }
</style>
</head>
<body>

<section class="card card--back" aria-label="Card back – appointment">
  <div class="brand">
    <span class="brand__dot"></span>
    <span class="brand__name">Brightfield<br>Nutrition &amp; Dietetics</span>
  </div>

  <div class="badge">
    <span class="badge__text">Certified Clinical Nutritionist</span>
    <span class="badge__seal"></span>
  </div>

  <div class="form-line" style="top:70px"></div>
  <div class="form-line" style="top:96px"></div>
  <span class="form-label" style="left:22px;top:108px">Date :</span>
  <div class="form-line" style="top:124px;left:70px"></div>
  <div class="form-line" style="top:150px"></div>
  <span class="form-label" style="left:22px;top:166px">Time :</span>
  <div class="form-line" style="top:182px;left:70px;right:80px"></div>
  <span class="form-ampm" style="right:28px;top:174px">AM/PM</span>

  <ul class="locations locations--left">
    <li>Pinebrook Medical Centre</li>
    <li>North Corrin Health</li>
  </ul>
  <ul class="locations locations--right">
    <li>Ashcombe Doctors Surgery</li>
    <li>Hollis Medical</li>
  </ul>
</section>

<section class="card card--front" aria-label="Card front – contact">
  <div class="brand">
    <span class="brand__dot"></span>
    <span class="brand__name">Brightfield<br>Nutrition &amp; Dietetics</span>
  </div>

  <div class="divider"></div>

  <div class="person">
    <h1 class="person__name">Marcus Kellaway</h1>
    <p class="person__role">Nutritionist &amp; Chef</p>
  </div>

  <ul class="contacts">
    <li><svg viewBox="0 0 16 16" aria-hidden="true"><path d="M3 1h3l1 4-2 1a9 9 0 0 0 5 5l1-2 4 1v3a2 2 0 0 1-2 2A13 13 0 0 1 1 3a2 2 0 0 1 2-2z"/></svg>0427 561 903</li>
    <li><svg viewBox="0 0 16 16" aria-hidden="true"><path d="M4 1h7v4H4zM2 6h12v7h-2v2H4v-2H2zm3 5v3h6v-3z"/></svg>6457 2183</li>
    <li><svg viewBox="0 0 16 16" aria-hidden="true"><path d="M1 3h14v10H1zm1 1v.5l6 4 6-4V4z"/></svg>marcus.k.diet@fernmail.com</li>
    <li><svg viewBox="0 0 16 16" aria-hidden="true"><circle cx="8" cy="8" r="7"/></svg>www.brightfieldnutrition.com.au</li>
  </ul>
</section>

</body>
</html>
```